Need help in designing new business card utilizing our new logo.

BuildMark Solutions works with Construction Business Owners, Managers & IT Professionals to strengthen software usage and increase user productivity.

Our Construction Accounting and Mobile Field Management Software Clients engage with us in the following areas:

New Software Implementations
Software Re-Implementations
Redesigning Software Usage at the User Level
Project Coordination & Management
Continued Software Support

Old tag line:
Weighing Options - Implementing Solutions

www.buildmark-solutions.example

Ridge 4 is a product, but not needed for a new business card.

```html
<!DOCTYPE html>
<html lang="en">
<head>
<meta charset="utf-8">
<title>BuildMark Solutions – Business Card</title>
<link href="https://fonts.googleapis.com/css2?family=Oswald:wght@500&family=Questrial&display=swap" rel="stylesheet">
<style>
  :root {
    --backdrop: #232325;
    --card: #3b3b3d;
    --brand-blue: #2c37a6;
    --light-grey: #d8d8da;
    --muted: #bdbdc0;
    --faint: #47474a;
  }
  * { margin: 0; padding: 0; box-sizing: border-box; }
  html, body {
    width: 1200px; height: 800px; overflow: hidden;
    background: var(--backdrop);
  }
  .canvas {
    position: relative; width: 1200px; height: 800px;
    display: flex; flex-direction: column; align-items: center; justify-content: center;
    gap: 40px;
  }
  .card {
    position: relative; width: 600px; height: 343px;
    background: var(--card);
    box-shadow: 0 10px 28px rgba(0,0,0,.45);
    overflow: hidden;
    font-family: "Questrial", "Century Gothic", sans-serif;
  }
  /* back side */
  .back-mark {
    position: absolute; right: 70px; top: 30px;
    width: 210px; height: 210px;
    background: var(--faint);
  }
  .back-wordmark {
    position: absolute; left: 36px; bottom: 36px;
    display: flex; align-items: center; gap: 12px;
  }
  .back-wordmark .dot {
    width: 22px; height: 22px; background: var(--brand-blue);
  }
  .wordmark {
    color: var(--brand-blue);
    text-transform: uppercase;
    letter-spacing: 3px;
    font-size: 20px;
    white-space: nowrap;
  }
  /* front side */
  .front-wordmark {
    position: absolute; left: 40px; top: 36px;
    font-size: 26px; letter-spacing: 4px; line-height: 1.12;
  }
  .front-wordmark span { display: block; }
  .front-mark {
    position: absolute; right: 44px; top: 48px;
    width: 190px; height: 190px;
    background: var(--brand-blue);
  }
  .person { position: absolute; left: 40px; top: 112px; }
  .person .name {
    font-family: "Oswald", "Arial Narrow", sans-serif;
    font-weight: 500; font-size: 22px; letter-spacing: 1px;
    color: #ffffff; text-transform: uppercase;
  }
  .person .role { color: var(--muted); font-size: 14px; margin-top: -2px; }
  .address {
    position: absolute; left: 40px; top: 188px;
    color: var(--muted); font-size: 12.5px; line-height: 1.4; font-style: normal;
  }
  .contacts {
    position: absolute; left: 40px; top: 236px;
    list-style: none; color: var(--light-grey); font-size: 12.5px;
  }
  .contacts li { display: flex; align-items: center; gap: 9px; height: 19px; }
  .contacts svg { width: 12px; height: 12px; fill: none; stroke: var(--brand-blue); stroke-width: 2; }
  .contacts svg .solid { fill: var(--brand-blue); stroke: none; }
</style>
</head>
<body>
<main class="canvas">

  <section class="card card-back" aria-label="Card back">
    <div class="back-mark" aria-hidden="true"></div>
    <div class="back-wordmark">
      <span class="dot" aria-hidden="true"></span>
      <span class="wordmark">BuildMark Solutions</span>
    </div>
  </section>

  <section class="card card-front" aria-label="Card front">
    <div class="wordmark front-wordmark"><span>BuildMark</span><span>Solutions</span></div>
    <div class="front-mark" aria-hidden="true"></div>

    <div class="person">
      <div class="name">Dana R. Whitfield</div>
      <div class="role">Owner</div>
    </div>

    <address class="address">
      48b Market Street - PMB 117<br>
      Riverton NY 12040
    </address>

    <ul class="contacts">
      <li>
        <svg viewBox="0 0 12 12"><path d="M2 1.5c0 5 3.5 8.5 8.5 8.5l.5-2-2.5-1-1 1c-1.5-.7-2.8-2-3.5-3.5l1-1-1-2.5z" class="solid"/></svg>
        800-555-0142 ext.100
      </li>
      <li>
        <svg viewBox="0 0 12 12"><rect x="3" y="1" width="6" height="10" rx="1"/></svg>
        555-014-7788
      </li>
      <li>
        <svg viewBox="0 0 12 12"><rect x="1" y="2.5" width="10" height="7" class="solid"/><path d="M1 3l5 3.5L11 3" stroke="#3b3b3d" stroke-width="1.2"/></svg>
        dana.whitfield@buildmark-solutions.example
      </li>
      <li>
        <svg viewBox="0 0 12 12"><circle cx="6" cy="6" r="4.5"/><path d="M1.5 6h9M6 1.5c-2 3-2 6 0 9M6 1.5c2 3 2 6 0 9" stroke-width="1"/></svg>
        www.buildmark-solutions.example
      </li>
    </ul>
  </section>

</main>
</body>
</html>
```